Document Processing Services and Solutions for School Systems

I am looking to design a brochure for both Digital and Paper use. I can supply the written content. Would be looking for an overall design of the brochure with provided content worked into it.

```html
<!DOCTYPE html>
<html lang="en">
<head>
<meta charset="utf-8">
<title>Meridian – School Document Solutions Brochure</title>
<link href="https://fonts.googleapis.com/css2?family=Poppins:wght@400;500;600;700;800&family=Open+Sans:wght@400;600&display=swap" rel="stylesheet">
<style>
:root{
  --navy:#2a2a8c;
  --navy-deep:#1f1f6e;
  --gold:#f2ae1c;
  --ink:#1d1d3a;
  --text:#44465a;
  --paper:#ffffff;
  --stage:#e9eaee;
}
*{box-sizing:border-box;margin:0;padding:0}
html,body{width:1200px;height:2700px;overflow:hidden}
body{background:var(--stage);font-family:"Open Sans",Arial,sans-serif;color:var(--text);position:relative}
h1,h2,h3,h4,.heading{font-family:"Poppins",Arial,sans-serif}
.spread{position:absolute;left:40px;width:1120px;height:780px;background:var(--paper);display:flex;box-shadow:0 6px 24px rgba(20,20,60,.12);overflow:hidden}
.spread--outside{top:320px}
.spread--inside{top:1440px;flex-direction:column}
.panel{position:relative;width:373.33px;height:100%}
.panel + .panel{border-left:1px solid #eceef3}
.photo{position:absolute;background:linear-gradient(135deg,#8c8f9c,#c9b79c 55%,#5d5f74)}

/* Why choose us */
.why{padding:60px 40px 0 44px}
.why h2{font-size:40px;line-height:1.05;font-weight:800;color:var(--navy-deep)}
.why h2 span{color:var(--gold)}
.why .rule{width:60px;height:4px;background:var(--gold);margin:14px 0 30px}
.benefit{display:flex;gap:16px;margin-bottom:28px}
.benefit .icon{flex:0 0 46px;height:46px;border-radius:50%;background:var(--gold);display:flex;align-items:center;justify-content:center}
.benefit h3{font-size:19px;font-weight:600;color:var(--navy);line-height:1.15}
.benefit p{font-size:12px;line-height:1.45;margin-top:8px;margin-left:-62px}
.benefit .copy{padding-top:2px}

/* Get started */
.start-band{position:absolute;left:0;top:0;width:100%;height:270px;background:var(--navy)}
.quote{position:absolute;font-family:"Poppins",sans-serif;font-weight:800;font-size:64px;color:var(--gold);line-height:1}
.start-band h2{position:absolute;left:70px;top:40px;font-size:30px;font-weight:700;line-height:1.15;color:var(--gold)}
.start-band p{position:absolute;left:70px;top:118px;width:240px;font-size:12px;line-height:1.45;color:#dfe0f5}
.start-photo-accent{position:absolute;left:60px;top:172px;width:280px;height:240px;background:var(--gold)}
.contact{position:absolute;left:40px;top:440px;right:36px}
.contact .lead{font-size:15px;color:var(--navy);font-weight:600}
.contact h3{font-size:24px;font-weight:700;color:var(--navy-deep);line-height:1.15}
.contact p.note{font-size:12px;line-height:1.45;margin-top:8px}
.contact ul{list-style:none;margin-top:22px}
.contact li{display:flex;align-items:center;gap:12px;font-size:13px;font-weight:600;color:var(--ink);margin-bottom:14px}
.dot-icon{width:30px;height:30px;border-radius:50%;background:var(--gold);display:flex;align-items:center;justify-content:center}

/* Cover */
.brand{position:absolute;right:40px;top:40px;display:flex;align-items:center;gap:10px}
.brand .mark{width:18px;height:18px;background:var(--gold)}
.brand .name{font-family:"Poppins",sans-serif;font-weight:700;font-size:34px;color:var(--navy)}
.cover-bar{position:absolute;left:0;top:130px;width:100%;height:14px;background:var(--navy)}
.cover-gold{position:absolute;right:0;top:160px;width:14px;height:230px;background:var(--gold)}
.cover h1{position:absolute;left:36px;top:418px;width:310px;font-size:25px;font-weight:800;line-height:1.12;color:var(--navy);text-transform:uppercase}
.cover h1 small{display:block;font-size:17px;text-transform:none;font-weight:600;color:var(--ink);margin-top:4px}
.cover h1 small b{color:var(--navy)}
.cover h4{position:absolute;left:36px;top:560px;font-size:14px;font-weight:700;color:var(--ink)}
.cover p{position:absolute;left:36px;top:584px;width:300px;font-size:11.5px;line-height:1.5}
.cover-foot{position:absolute;left:0;bottom:0;width:100%;height:56px;background:var(--navy);display:flex;align-items:center;justify-content:center;font-family:"Poppins",sans-serif;font-weight:600;font-size:15px;color:var(--gold);letter-spacing:.5px}
.cover-foot::before{content:"";position:absolute;left:0;top:-8px;width:100%;height:8px;background:var(--gold)}

/* Inside */
.services-band{height:76px;background:var(--navy);display:flex;align-items:center;justify-content:center;border-bottom:6px solid var(--gold)}
.services-band h2{font-size:34px;font-weight:700;color:#fff}
.inside-panels{display:flex;flex:1}
.inside-panels .panel{height:auto}
.services-foot{height:26px;background:var(--navy)}
.service-head{display:flex;gap:14px;align-items:center}
.square-icon{flex:0 0 52px;height:52px;display:flex;align-items:center;justify-content:center}
.square-icon--gold{background:var(--gold)}
.square-icon--navy{background:var(--navy)}
.service-head h3{font-size:21px;font-weight:700;color:var(--navy-deep);line-height:1.12}
.ticks{list-style:none;margin-top:18px}
.ticks li{position:relative;padding-left:24px;font-size:12px;line-height:1.45;margin-bottom:12px}
.ticks li::before{content:"";position:absolute;left:0;top:3px;width:13px;height:13px;border-radius:50%;background:var(--navy)}
.ticks li::after{content:"";position:absolute;left:4px;top:6px;width:4px;height:6px;border:solid #fff;border-width:0 1.6px 1.6px 0;transform:rotate(45deg)}
.ticks--gold li::before{background:var(--gold)}
.service{position:absolute;left:34px;right:30px}
.frame-gold{position:absolute;background:var(--gold)}
</style>
</head>
<body>

<!-- Outside spread -->
<section class="spread spread--outside">

  <div class="panel why">
    <h2>Why Choose<br><span>Us?</span></h2>
    <div class="rule"></div>

    <div class="benefit">
      <div class="icon"><svg width="24" height="24" viewBox="0 0 24 24" fill="none" stroke="#fff" stroke-width="2.2"><path d="M3 20h18M5 16l5-5 4 3 6-7"/><path d="M15 7h5v5"/></svg></div>
      <div class="copy"><h3>Increased<br>Efficiency</h3></div>
    </div>
    <p class="benefit-note" style="font-size:12px;line-height:1.45;margin:-16px 0 22px">Save time with digital workflows and instant document retrieval.</p>

    <div class="benefit">
      <div class="icon"><svg width="22" height="24" viewBox="0 0 22 24" fill="none" stroke="#fff" stroke-width="2.2"><path d="M11 2 3 5v6c0 6 4 9 8 11 4-2 8-5 8-11V5z"/><path d="m7 12 3 3 5-6"/></svg></div>
      <div class="copy"><h3>Enhanced<br>Security</h3></div>
    </div>
    <p style="font-size:12px;line-height:1.45;margin:-16px 0 22px">Protect sensitive student and faculty information.</p>

    <div class="benefit">
      <div class="icon"><svg width="22" height="24" viewBox="0 0 22 24" fill="none" stroke="#fff" stroke-width="2.2"><path d="M11 2v20M16 6H8.5a3.5 3.5 0 0 0 0 7h5a3.5 3.5 0 0 1 0 7H5"/></svg></div>
      <div class="copy"><h3>Cost<br>Savings</h3></div>
    </div>
    <p style="font-size:12px;line-height:1.45;margin:-16px 0 22px">Reduce paper, printing, and storage costs.</p>

    <div class="benefit">
      <div class="icon"><svg width="24" height="24" viewBox="0 0 24 24" fill="none" stroke="#fff" stroke-width="2.2"><path d="M4 20c0-9 6-15 16-16-1 10-7 16-16 16z"/><path d="M4 20 13 11"/></svg></div>
      <div class="copy"><h3>Eco<br>Friendly</h3></div>
    </div>
    <p style="font-size:12px;line-height:1.45;margin:-16px 0 0">Minimize your school's carbon footprint by going digital.</p>
  </div>

  <div class="panel start">
    <div class="start-band">
      <span class="quote" style="left:24px;top:30px">&ldquo;</span>
      <h2>GET STARTED<br>TODAY!</h2>
      <p>Let us help you modernize your school's document processing system.</p>
    </div>
    <div class="start-photo-accent"></div>
    <div class="photo" role="img" aria-label="Photo of two school staff members smiling while working together at a desk" style="left:40px;top:186px;width:280px;height:220px;background:linear-gradient(135deg,#6e6f86,#caa98a 50%,#3f4260)"></div>
    <span class="quote" style="left:300px;top:388px">&rdquo;</span>

    <div class="contact">
      <div class="lead">Contact us for a</div>
      <h3>free consultation</h3>
      <p class="note">and discover how our solutions can transform your school's document management.</p>
      <ul>
        <li><span class="dot-icon"><svg width="14" height="14" viewBox="0 0 24 24" fill="#fff"><path d="M6.6 10.8a15 15 0 0 0 6.6 6.6l2.2-2.2c.3-.3.7-.4 1-.2 1.1.4 2.3.6 3.6.6.6 0 1 .4 1 1V20c0 .6-.4 1-1 1A17 17 0 0 1 3 4c0-.6.4-1 1-1h3.5c.6 0 1 .4 1 1 0 1.3.2 2.5.6 3.6.1.3 0 .7-.2 1z"/></svg></span>000-000-0000</li>
        <li><span class="dot-icon"><svg width="14" height="14" viewBox="0 0 24 24" fill="none" stroke="#fff" stroke-width="2.4"><rect x="3" y="5" width="18" height="14" rx="1"/><path d="m3 6 9 7 9-7"/></svg></span>info@meridiandocs.com</li>
        <li><span class="dot-icon"><svg width="14" height="14" viewBox="0 0 24 24" fill="none" stroke="#fff" stroke-width="2.2"><circle cx="12" cy="12" r="9"/><path d="M3 12h18M12 3c3 3 3 15 0 18M12 3c-3 3-3 15 0 18"/></svg></span>www.meridiandocs.com</li>
      </ul>
    </div>
  </div>

  <div class="panel cover">
    <div class="brand"><span class="mark"></span><span class="name">Meridian</span></div>
    <div class="cover-bar"></div>
    <div class="cover-gold"></div>
    <div class="photo" role="img" aria-label="Photo of a bright modern classroom with students working at computers" style="left:36px;top:160px;width:323px;height:230px;background:linear-gradient(135deg,#b7a58a,#e2d6c2 45%,#6c6a74)"></div>
    <h1>Transform your school's document management<small>with our <b>Comprehensive Solutions</b></small></h1>
    <h4>Streamline, Secure, and Simplify</h4>
    <p>Managing records in schools should be efficient, secure, and accessible. Our document processing services help administrators, teachers, and staff spend less time on paperwork and more time on students.</p>
    <div class="cover-foot">www.meridiandocs.com</div>
  </div>
</section>

<!-- Inside spread -->
<section class="spread spread--inside">
  <header class="services-band"><h2>Our Services</h2></header>

  <div class="inside-panels">
    <div class="panel">
      <div class="photo" role="img" aria-label="Photo of a staff member working at a computer in a school office" style="left:34px;top:24px;width:300px;height:250px;background:linear-gradient(135deg,#3d3f5e,#9d8f86 55%,#d9d2c6)"></div>
      <div class="service" style="top:300px">
        <div class="service-head">
          <div class="square-icon square-icon--gold"><svg width="28" height="28" viewBox="0 0 24 24" fill="none" stroke="#fff" stroke-width="2"><path d="M6 2h9l4 4v16H6z"/><path d="M3 13h18"/></svg></div>
          <h3>Document<br>Scanning &amp;<br>Conversion</h3>
        </div>
        <ul class="ticks ticks--gold">
          <li>Convert paper records into digital formats for easy access and storage.</li>
          <li>High-speed scanning for large volumes of administrative, financial, and historical archives.</li>
          <li>OCR (Optical Character Recognition) for searchable and editable documents.</li>
        </ul>
      </div>
    </div>

    <div class="panel">
      <div class="service" style="top:28px">
        <div class="service-head">
          <div class="square-icon square-icon--navy"><svg width="30" height="30" viewBox="0 0 24 24" fill="none" stroke="#fff" stroke-width="2"><path d="M7 18h11a4 4 0 0 0 0-8 6 6 0 0 0-11.5 1A3.5 3.5 0 0 0 7 18z"/></svg></div>
          <h3>Cloud-Based<br>Document<br>Management</h3>
        </div>
        <ul class="ticks">
          <li>Secure, centralized document storage accessible from anywhere.</li>
          <li>Role-based access controls for administrators, teachers, and staff.</li>
          <li>Automated backups and compliance with educational data security standards.</li>
        </ul>
      </div>
      <div class="frame-gold" style="left:60px;top:420px;width:262px;height:238px"></div>
      <div class="photo" role="img" aria-label="Photo of hands holding a tablet with glowing cloud and document icons" style="left:48px;top:408px;width:262px;height:238px;background:radial-gradient(circle at 50% 40%,#5b84d8,#1d2a6e 60%,#0e1440)"></div>
    </div>

    <div class="panel">
      <div class="photo" role="img" aria-label="Photo of a busy open-plan school administration office" style="left:30px;top:24px;width:310px;height:250px;background:linear-gradient(135deg,#cfc6b4,#8d8a86 50%,#3a3d52)"></div>
      <div class="service" style="top:300px">
        <div class="service-head">
          <div class="square-icon square-icon--gold"><svg width="28" height="28" viewBox="0 0 24 24" fill="none" stroke="#fff" stroke-width="2"><circle cx="12" cy="12" r="3"/><path d="M12 2v3M12 19v3M2 12h3M19 12h3M5 5l2 2M17 17l2 2M5 19l2-2M17 7l2-2"/></svg></div>
          <h3>Workflow<br>Automation</h3>
        </div>
        <ul class="ticks ticks--gold">
          <li>Digitize and streamline approval processes for enrollment, transcripts, and HR forms.</li>
          <li>Reduce paperwork and improve efficiency with automated workflows.</li>
          <li>Integration with existing school management systems.</li>
        </ul>
      </div>
    </div>
  </div>
  <div class="services-foot"></div>
</section>

</body>
</html>
```